RW Framewell Inc Business cards

We need business cards using our existing logo but slightly modified. Right now the logo says RW Loadbearing Masonry. We want to keep the RW part of the design, but replace the Structural Concrete portion with "FRAMEWELL". Please see the attached file.
Ideally this would be a blank template so we can add Different Names, titles, and phone numbers later.
On the one side we want only the logo and on the other side the detail. I'm attaching an example for you to see.
Please reach out with any other questions. Our address and other details will be given out once we find a design we like.

Target Market(s)

Construction Industry

```html
<!DOCTYPE html>
<html lang="en">
<head>
<meta charset="UTF-8">
<title>RW Framewell Inc Business Cards</title>
<link rel="stylesheet" href="https://fonts.googleapis.com/css2?family=Montserrat:wght@400;500;600;700&display=swap">
<style>
  :root {
    --backdrop: #d6d6d6;
    --card: #f8f8f8;
    --brand-blue: #2f5fab;
    --brand-grey: #5f5f5f;
    --text-grey: #555555;
    --ghost: #e9e9e9;
  }
  * { margin: 0; padding: 0; box-sizing: border-box; }
  html, body {
    width: 1200px;
    height: 852px;
    overflow: hidden;
    background: var(--backdrop);
    font-family: "Montserrat", Arial, sans-serif;
  }
  .stage { position: relative; width: 1200px; height: 852px; }

  .card {
    position: absolute;
    width: 500px;
    height: 290px;
    background: var(--card);
    border-radius: 18px;
    overflow: hidden;
  }

  /* Front: logo only */
  .card--front { left: 90px; top: 110px; }
  .card--front .wordmark {
    position: absolute;
    left: 0; right: 0; top: 92px;
    text-align: center;
    color: var(--brand-blue);
    font-weight: 600;
  }
  .wordmark .initials { display: block; font-size: 64px; line-height: 1; letter-spacing: 2px; }
  .wordmark .name { display: block; font-size: 22px; letter-spacing: 7px; margin-top: 6px; }
  .edge-band {
    position: absolute; left: 0; right: 0; bottom: 0; height: 12px; display: flex;
  }
  .edge-band .band-grey { width: 38%; background: var(--brand-grey); }
  .edge-band .band-blue { flex: 1; background: var(--brand-blue); }

  /* Back: details */
  .card--back { left: 610px; top: 440px; }
  .ghost-mark {
    position: absolute; left: 170px; top: 20px;
    font-size: 190px; font-weight: 600; color: var(--ghost);
    line-height: 1; letter-spacing: 4px;
  }
  .side-tab {
    position: absolute; left: -22px; top: 46px;
    width: 44px; height: 44px; border-radius: 50%;
    background: var(--brand-blue);
  }
  .person { position: absolute; left: 38px; top: 48px; }
  .person .full-name { font-size: 19px; font-weight: 700; color: var(--brand-blue); }
  .person .role { font-size: 12px; color: var(--text-grey); margin-top: 3px; }

  .card--back .wordmark {
    position: absolute; right: 30px; top: 80px;
    text-align: center; color: var(--brand-blue); font-weight: 600;
  }
  .card--back .wordmark .initials { font-size: 56px; }
  .card--back .wordmark .name { font-size: 19px; letter-spacing: 6px; }

  .details { position: absolute; left: 38px; top: 170px; width: 210px; }
  .address { font-size: 12px; line-height: 1.45; color: var(--text-grey); }
  .divider { height: 1.5px; background: var(--brand-blue); margin: 7px 0 8px; }
  .contact-list { list-style: none; }
  .contact-list li {
    display: flex; align-items: center; gap: 10px;
    font-size: 12px; color: var(--text-grey); line-height: 1.55;
  }
  .contact-list svg { width: 11px; height: 11px; fill: var(--brand-blue); flex: none; }
</style>
</head>
<body>
<main class="stage">

  <section class="card card--front" aria-label="Business card front">
    <div class="wordmark">
      <span class="initials">RW</span>
      <span class="name">FRAMEWELL</span>
    </div>
    <div class="edge-band"><span class="band-grey"></span><span class="band-blue"></span></div>
  </section>

  <section class="card card--back" aria-label="Business card back">
    <div class="ghost-mark" aria-hidden="true">RW</div>
    <span class="side-tab"></span>

    <div class="person">
      <p class="full-name">Mark RW Ellison</p>
      <p class="role">Managing Director</p>
    </div>

    <div class="wordmark">
      <span class="initials">RW</span>
      <span class="name">FRAMEWELL</span>
    </div>

    <div class="details">
      <p class="address">58 Sample Rd., Any Town,<br>Oregon, US 970001</p>
      <div class="divider"></div>
      <ul class="contact-list">
        <li>
          <svg viewBox="0 0 24 24" aria-hidden="true"><path d="M6.6 10.8a15.1 15.1 0 0 0 6.6 6.6l2.2-2.2a1 1 0 0 1 1-.25 11.4 11.4 0 0 0 3.6.57 1 1 0 0 1 1 1V20a1 1 0 0 1-1 1A17 17 0 0 1 3 4a1 1 0 0 1 1-1h3.5a1 1 0 0 1 1 1c0 1.25.2 2.45.57 3.57a1 1 0 0 1-.25 1z"/></svg>
          555-010-2020
        </li>
        <li>
          <svg viewBox="0 0 24 24" aria-hidden="true"><path d="M2 5h20v14H2zm2 2v.5l8 5 8-5V7l-8 5z"/></svg>
          mark@framewell.example
        </li>
        <li>
          <svg viewBox="0 0 24 24" aria-hidden="true"><circle cx="12" cy="12" r="10"/></svg>
          www.framewell.example
        </li>
      </ul>
    </div>
  </section>

</main>
</body>
</html>
```